NZ First of it's kind solutions directory and marketplace for busy Mums needs a business card design

We need a business card design for our new nationwide business in NZ (long term plans to go global). We provide solutions to the everyday challenges that busy Mums face by connecting them with quality communities and suppliers of carefully selected, relevant products and services. We sell direct via our online marketplace. The final design should communicate our values of inclusivity, quality and smart solutions. Colours should incorporate our logo colour palette of #477077 and #6ba8b2. Our website is at https://www.brightnestmums.example

Target Market(s)

busy Mums, Age 28 – 50, female, income over $100K, location main centres NZ primarily but NZ wide. Is likely juggling work or career with a young family. Probably had hobbies which have fallen by the wayside.
-Wants to succeed in her chosen career without compromising on family life
-to successfully juggle her career without feeling like she is compromising her children
- Is time poor, something always has to give and it’s generally her health (she’ll stay up late, get stressed)
- probably ex corporate or professional career. Has discretional income

Industry/Entity Type

Business

Contact Information for Business Card

Lena Forbisher, Founder, BrightNestMums.example (Strapline Tap; Gather; Sorted), 47 Kowhai Terrace, Ellerslie, Auckland 1051, New Zealand. Mob: 021 483 517 Ph: +64 (0)9 571 4860

Font styles to use
Other font styles liked:
• Raleway, and/or Architects Daughter

Colors
00a990
33b8a4
86cfc6
cfeae6

Requirements
Must have
• the above details, streamline. the logo and colours associated with those logos
Should not have
• foil or metallic colours

```html
<!DOCTYPE html>
<html lang="en">
<head>
<meta charset="utf-8">
<title>BrightNestMums – Business Card</title>
<link rel="stylesheet" href="https://fonts.googleapis.com/css2?family=Varela+Round&family=Roboto:wght@400&family=Roboto+Condensed:ital,wght@0,400;1,400&display=swap">
<style>
  :root {
    --brand-deep: #477077;
    --brand-light: #6ba8b2;
    --card-back: #3e5f66;
    --card-front: #f7f7f7;
    --ink-dark: #3a3f41;
    --text-light: #ffffff;
    --text-soft: #e4eef0;
    --backdrop: #e6e6e6;
  }
  * { box-sizing: border-box; margin: 0; padding: 0; }
  html, body {
    width: 1200px; height: 576px; overflow: hidden;
    background: var(--backdrop);
  }
  .canvas { position: relative; width: 1200px; height: 576px; }

  .card {
    position: absolute; top: 138px;
    width: 482px; height: 293px;
    border-radius: 14px; overflow: hidden;
  }
  .card--front { left: 82px; background: var(--card-front); }
  .card--back { left: 602px; background: var(--card-back); color: var(--text-light); }

  /* Front */
  .brand-dot {
    position: absolute; left: 30px; top: 128px;
    width: 120px; height: 120px; border-radius: 50%;
    background: var(--brand-deep);
  }
  .wordmark {
    position: absolute; right: 32px; top: 196px;
    font-family: "Varela Round", sans-serif;
    font-size: 31px; line-height: 1;
    color: var(--brand-deep);
    letter-spacing: -0.5px;
  }
  .strapline {
    position: absolute; right: 30px; top: 236px;
    font-family: "Roboto", sans-serif;
    font-size: 11px; letter-spacing: 3.6px;
    color: var(--ink-dark); text-transform: uppercase;
  }
  .strapline .divider { color: var(--brand-light); margin: 0 4px; }

  /* Back */
  .identity {
    position: absolute; right: 262px; top: 112px;
    text-align: right;
    font-family: "Roboto Condensed", sans-serif;
  }
  .identity__name {
    font-family: "Varela Round", sans-serif;
    font-size: 19px; line-height: 22px; font-weight: 400;
    -webkit-text-stroke: 0.4px var(--text-light);
  }
  .identity__role { font-style: italic; font-size: 12px; color: var(--text-soft); margin-top: 1px; }
  .identity__address { font-size: 12.5px; line-height: 18px; color: var(--text-soft); margin-top: 9px; }

  .contact-list {
    position: absolute; left: 244px; top: 114px;
    list-style: none;
    font-family: "Roboto Condensed", sans-serif;
    font-size: 12.5px; color: var(--text-soft);
  }
  .contact-list li { display: flex; align-items: center; height: 18.5px; }
  .contact-list svg { width: 11px; height: 11px; margin-right: 8px; fill: var(--text-soft); flex: none; }
</style>
</head>
<body>
<main class="canvas">

  <section class="card card--front" aria-label="Card front">
    <span class="brand-dot" aria-hidden="true"></span>
    <h1 class="wordmark">BrightNestMums</h1>
    <p class="strapline">Tap<span class="divider">|</span>Gather<span class="divider">|</span>Sorted</p>
  </section>

  <section class="card card--back" aria-label="Card back">
    <div class="identity">
      <h2 class="identity__name">Lena Forbisher</h2>
      <p class="identity__role">Founder</p>
      <p class="identity__address">47 Kowhai Terrace, Ellerslie,<br>Auckland 1051, New Zealand</p>
    </div>

    <ul class="contact-list">
      <li>
        <svg viewBox="0 0 12 12" aria-hidden="true"><path d="M3 0h6a1 1 0 0 1 1 1v10a1 1 0 0 1-1 1H3a1 1 0 0 1-1-1V1a1 1 0 0 1 1-1zm0 2v7h6V2zm3 8a.7.7 0 1 0 0 1.4A.7.7 0 0 0 6 10z"/></svg>
        021 483 517
      </li>
      <li>
        <svg viewBox="0 0 12 12" aria-hidden="true"><path d="M0 4c0-2 3-3 6-3s6 1 6 3v1H9V3.5C8 3 4 3 3 3.5V5H0zm2 2h8l1 5H1zm4 1.2a1.6 1.6 0 1 0 0 3.2 1.6 1.6 0 0 0 0-3.2z"/></svg>
        +64 (0)9 571 4860
      </li>
      <li>
        <svg viewBox="0 0 12 12" aria-hidden="true"><path d="M0 2h12v8H0zm1 1v.4l5 3.4 5-3.4V3zm0 1.6V9h10V4.6L6 8z"/></svg>
        www.BrightNestMums.example
      </li>
      <li>
        <svg viewBox="0 0 12 12" aria-hidden="true"><path d="M6 0a6 6 0 1 0 0 12A6 6 0 0 0 6 0zm0 1c.8 0 1.6 1.6 1.9 4H4.1C4.4 2.6 5.2 1 6 1zM1.1 5h2a11 11 0 0 1 .6-3.4A5 5 0 0 0 1.1 5zm7.8 0h2a5 5 0 0 0-2.6-3.4c.3 1 .5 2.1.6 3.4zM1.1 7a5 5 0 0 0 2.6 3.4A11 11 0 0 1 3.1 7zm3 0c.3 2.4 1.1 4 1.9 4s1.6-1.6 1.9-4zm4.8 0a11 11 0 0 1-.6 3.4A5 5 0 0 0 10.9 7z"/></svg>
        lenaforbisher@brightnestmums.example
      </li>
    </ul>
  </section>

</main>
</body>
</html>
```